QRV Advisors needs a web site

We need a web site for www.qrvadvisors-example.com. QRV is a mergers and acquisition consulting company that focuses our buyer and seller services on logistics companies. We help put companies together, and help with legal and financial due diligence. We want the web site to express our service and show the logistics components. We want personalized images versus pictures of trucks and airplanes.

Our new logo uses Burgandy and grey colors. Image attached. We are not in to bold, big letters...classy, artistic, low key preferred. Confidentiality, experience, professional are what we want to express on the site.

All we expect for the first part of this project is a home page, and one subpage.  We are budgeting other funds for the technical aspects of the web site

Reason: All that I'm seeing so far is trucks, forklifts and planes. We are a legal mergers and acquisitions firm that focus on logistics. I like some of the images to say logistics, but really want it say legal, financial, and putting companies together. Will pay extra for the sub page if someone can impress us with a home page.

Reason: Swamped with another project at the moment...will work on this over the weekend and provide designer feedback and select final design by Tuesday

```html
<!DOCTYPE html>
<html lang="en">
<head>
<meta charset="utf-8">
<title>QRV Advisors</title>
<link href="https://fonts.googleapis.com/css2?family=Ubuntu:wght@400;500&family=Open+Sans:wght@400;600;700&display=swap" rel="stylesheet">
<style>
:root{
  --burgundy:#a1093a;
  --burgundy-dark:#7d0029;
  --ink:#333;
  --muted:#555;
  --panel:#f3f3f3;
  --footer:#0d0d0d;
  --blue-deep:#0a4f8a;
  --blue-light:#29b6e8;
}
*{box-sizing:border-box;margin:0;padding:0}
html,body{width:1063px;height:1200px;overflow:hidden}
body{position:relative;background:#fff;font-family:"Open Sans",sans-serif;color:var(--ink)}
.abs{position:absolute}
.top-band{left:0;top:0;width:1063px;height:407px;background:linear-gradient(#fafafa,#e4e4e4)}
.brand{left:141px;top:36px;display:flex;align-items:center;gap:10px}
.brand-mark{width:22px;height:22px;background:var(--burgundy)}
.brand-name{font-family:"Ubuntu",sans-serif;font-weight:400;font-size:36px;color:var(--burgundy);letter-spacing:1px}
.call{right:143px;top:43px;font-family:"Ubuntu",sans-serif;font-size:18px;color:#444;display:flex;align-items:center;gap:6px}
.call b{font-weight:500}
.nav{left:140px;top:105px;width:781px;height:34px;background:linear-gradient(#b01444,var(--burgundy-dark));border:2px solid #d0c9cb;border-radius:3px;display:flex;align-items:center;padding:0 8px;justify-content:space-between;font-family:"Ubuntu",sans-serif;font-size:11.6px;color:#fff}
.nav span{padding:4px 12px}
.nav .current{background:#fff;color:#666;border-radius:2px}
.hero-frame{left:137px;top:152px;width:788px;height:312px;background:#fff;border-radius:4px;box-shadow:0 6px 8px rgba(0,0,0,.15)}
.hero{left:141px;top:155px;width:781px;height:306px;border-radius:3px;background:radial-gradient(circle at 72% 60%,var(--blue-light),var(--blue-deep) 75%)}
.tag{left:582px;top:255px;border:1px solid #cfe;border-radius:2px;padding:1px 5px;color:#fff;font-size:9px;background:rgba(0,60,110,.5)}
.headline{left:584px;top:286px;width:330px;font-family:"Ubuntu",sans-serif;font-size:20px;line-height:28px;color:#fff;text-shadow:0 1px 2px rgba(0,0,0,.5)}
.slider-tab{left:762px;top:432px;width:105px;height:29px;background:#f1f1f1;border-radius:5px 5px 0 0;display:flex}
.slider-tab div{flex:1;display:flex;align-items:center;justify-content:center;border-right:1px solid #ddd}
.box{background:linear-gradient(#efefef,#fafafa 60%,#fff);border:1px solid #e2e2e2}
.box h2{font-family:"Ubuntu",sans-serif;font-weight:400;font-size:19px;color:#555;padding:8px 12px 4px;border-bottom:2px solid var(--burgundy);margin:0 12px 0 0}
.box h2 em{font-style:normal;color:var(--burgundy)}
.welcome{left:140px;top:490px;width:508px;height:187px}
.welcome p{font-size:10.4px;line-height:15px;color:#333;padding:0 18px 0 11px;margin-top:10px;letter-spacing:.2px}
.more{position:absolute;font-size:10.4px;color:var(--burgundy);text-decoration:underline}
.news{left:674px;top:490px;width:249px;height:187px}
.news h2{margin:0 8px 0 12px;padding-left:0}
.item{display:flex;gap:14px;padding:8px 6px 6px 13px;border-bottom:1px dotted #556}
.date{width:36px;flex:none;text-align:center;font-family:"Ubuntu",sans-serif}
.date .m{background:var(--burgundy);color:#fff;font-size:10px;padding:1px 0}
.date .d{background:#d8d8d8;color:#333;font-size:14px;font-weight:500}
.item h3{font-size:11px;font-weight:600;color:var(--burgundy)}
.item p{font-size:9.6px;line-height:13px;color:#666;margin-top:3px}
.card{top:698px;width:244px}
.card .photo{height:132px;border:1px solid #ddd}
.card .bar{height:25px;background:var(--burgundy);color:#fff;font-family:"Ubuntu",sans-serif;font-size:15px;display:flex;align-items:center;justify-content:space-between;padding-left:19px;box-shadow:0 4px 5px rgba(0,0,0,.2)}
.card .go{width:33px;height:25px;background:#555;display:flex;align-items:center;justify-content:center}
.card p,.card ul{font-size:10.4px;line-height:16px;color:#333;padding:11px 8px 0}
.card ul{list-style:none;padding-left:14px}
.card li::before{content:"» ";font-size:9px}
.news-signup{left:139px;top:963px;width:784px;height:37px;border:1px solid #ddd;background:linear-gradient(#fff,#eee)}
.signup-label{left:0;top:0;height:35px;width:200px;background:var(--burgundy);clip-path:polygon(0 0,92% 0,100% 50%,92% 100%,0 100%);color:#fff;font-family:"Ubuntu",sans-serif;font-size:16px;display:flex;align-items:center;gap:8px;padding-left:10px}
.signup-text{left:207px;top:11px;font-size:10px;font-weight:700;color:#333}
.email{left:547px;top:8px;width:163px;height:20px;background:#ddd;border:1px solid #aaa;font-size:10.4px;color:#444;padding:2px 8px}
.submit{left:718px;top:8px;width:58px;height:20px;background:#555;color:#fff;font-size:11px;font-weight:600;text-align:center;line-height:20px}
.footer{left:0;top:1017px;width:1063px;height:183px;background:var(--footer);color:#fff}
.footer h4{font-family:"Ubuntu",sans-serif;font-weight:400;font-size:13.5px;border-bottom:1px solid #555;padding-bottom:2px}
.quick{left:142px;top:16px;width:88px}
.quick a{display:block;font-size:10px;font-weight:600;line-height:17.4px;color:#fff;text-decoration:none;padding-left:2px}
.locations{left:247px;top:16px;width:178px}
.map{left:247px;top:41px;width:187px;height:115px;background:linear-gradient(135deg,#e9e6df,#d8dfc9);border:2px solid #fff}
.contact{left:455px;top:16px;width:152px}
.contact-row{left:451px;display:flex;gap:9px;font-size:10.6px;line-height:14px;width:220px}
.follow{left:760px;top:24px;font-family:"Ubuntu",sans-serif;font-size:14px;display:flex;gap:8px;align-items:center}
.follow i{display:block;width:24px;height:24px;background:#bbb;border-radius:3px}
.foot-brand{left:683px;top:82px;font-family:"Ubuntu",sans-serif;font-size:32px;color:#fff;display:flex;gap:9px;align-items:center}
.foot-brand i{display:block;width:18px;height:18px;background:var(--burgundy)}
.copy{left:683px;top:129px;width:240px;text-align:center;font-size:11.5px;line-height:15px}
</style>
</head>
<body>
<div class="abs top-band"></div>

<div class="abs brand"><span class="brand-mark"></span><span class="brand-name">QRV Advisors</span></div>
<div class="abs call">
  <svg width="20" height="20" viewBox="0 0 20 20"><circle cx="10" cy="10" r="8.5" fill="none" stroke="#a1093a" stroke-width="1.5"/><path d="M7 5c-2 2-2 8 0 10l2-2c-1-2-1-4 0-6z" fill="#a1093a"/></svg>
  Call us <b>(555) 014-2290</b>
</div>

<nav class="abs nav">
  <span class="current">HOME</span><span>ABOUT US</span><span>BUYER SERVICES</span><span>SELLER SERVICES</span><span>NEWS &amp; EVENTS</span><span>FAQ's</span><span>CONTACT US</span>
</nav>

<div class="abs hero-frame"></div>
<div class="abs hero" role="img" aria-label="Businesswoman touching a glowing interface over a blue world map"></div>
<div class="abs tag">&#9656; Business Intelligence</div>
<div class="abs headline">QRV Services Are Offered By Industry Executives With Extensive M&amp;A Experience</div>
<div class="abs slider-tab">
  <div><svg width="20" height="10"><path d="M1 1l9 7 9-7" fill="none" stroke="#aaa" stroke-width="1.5"/></svg></div>
  <div><svg width="20" height="10"><path d="M1 9l9-7 9 7" fill="none" stroke="#aaa" stroke-width="1.5"/></svg></div>
</div>

<section class="abs box welcome">
  <h2>Welcome to <em>QRV Advisors</em></h2>
  <p>QRV assists business owners within the logistics industry to implement growth and exit strategies. We offer business planning and merger and acquisition(M&amp;A) advisory services. QRV services are offered by industry executives with extensive M&amp;A experience. Your company will benefit from a unique and outside perspective from consultants that understand your business.</p>
  <p>QRV can help you formulate and execute your growth strategy. We take a strategic and consultative approach with our advisory services ...</p>
  <a class="more" style="right:18px;top:175px">Read More »</a>
</section>

<section class="abs box news">
  <h2>News/Events</h2>
  <div class="item"><div class="date"><div class="m">MAR</div><div class="d">29</div></div><div><h3>Duis aute irure reprehenderit</h3><p>Lorem consectetur adipiscing elit. Morbi tristique sem.</p></div></div>
  <div class="item"><div class="date"><div class="m">APR</div><div class="d">01</div></div><div><h3>Duis aute irure reprehenderit</h3><p>Lorem consectetur adipiscing elit. Morbi tristique sem.</p></div></div>
  <a class="more" style="right:8px;top:175px">Read More »</a>
</section>

<article class="abs card" style="left:142px">
  <div class="photo" role="img" aria-label="Business partners shaking hands in an office" style="background:linear-gradient(#eef0f2,#b9b3ac)"></div>
  <div class="bar">What We Do<span class="go"><svg width="10" height="10"><path d="M1 5h6M4 2l3 3-3 3" stroke="#fff" stroke-width="2" fill="none"/></svg></span></div>
  <p>Lorem consectetur adipiscing elit. Morbi tristique sem. Nunc nec ipsum sed nisi Morbi tristique sem.Lorem consectetur adipiscing elit consectetur adi pis cing elit.</p>
  <a class="more" style="right:4px;top:236px">Read More »</a>
</article>
<article class="abs card" style="left:406px">
  <div class="photo" role="img" aria-label="Team meeting around a laptop and documents" style="background:linear-gradient(#f2f2f2,#a9a6a3)"></div>
  <div class="bar">Our Services<span class="go"><svg width="10" height="10"><path d="M1 5h6M4 2l3 3-3 3" stroke="#fff" stroke-width="2" fill="none"/></svg></span></div>
  <ul><li>Business Analysis</li><li>Business Intelligence</li><li>Mergers</li><li>Acquisition</li></ul>
  <a class="more" style="right:-4px;top:236px">Read More »</a>
</article>
<article class="abs card" style="left:671px">
  <div class="photo" role="img" aria-label="Figures walking through a grey maze" style="background:linear-gradient(#d4d4d4,#7d7d7d)"></div>
  <div class="bar">Our Mission<span class="go"><svg width="10" height="10"><path d="M1 5h6M4 2l3 3-3 3" stroke="#fff" stroke-width="2" fill="none"/></svg></span></div>
  <p>Lorem consectetur adipiscing elit. Morbi tristique sem. Nunc nec ipsum sed nisi Morbi tristique sem.Lorem consectetur adipiscing elit consectetur ad ipis cing elit.</p>
  <a class="more" style="right:-2px;top:236px">Read More »</a>
</article>

<div class="abs news-signup">
  <div class="abs signup-label">
    <svg width="16" height="16" viewBox="0 0 16 16"><path d="M2 3h7M2 3v11h11V8" fill="none" stroke="#fff" stroke-width="1.5"/><path d="M7 10l1-3 6-6 2 2-6 6z" fill="#fff"/></svg>
    Newsletter Signup
  </div>
  <div class="abs signup-text">Lorem ipsum doloronsectetur adipiscing elit. Morbi id tristique.</div>
  <div class="abs email">Email address</div>
  <div class="abs submit">SUBMIT</div>
</div>

<footer class="abs footer">
  <div class="abs quick"><h4>Quick Link</h4>
    <a>Home</a><a>About Us</a><a>Buyer Services</a><a>Seller Services</a><a>News &amp; Events</a><a>FAQ's</a><a>Contact us</a>
  </div>
  <div class="abs locations"><h4>QRV Locations</h4></div>
  <div class="abs map" role="img" aria-label="Street map of the office location"></div>
  <div class="abs contact"><h4>Contact Us</h4></div>
  <div class="abs contact-row" style="top:45px">
    <svg width="16" height="14" viewBox="0 0 16 14"><path d="M1 7l7-6 7 6M3 6v7h10V6" fill="none" stroke="#a1093a" stroke-width="1.5"/></svg>
    <span>Lorem consectetur adipiscing<br>elit. Morbi tristique sem.</span></div>
  <div class="abs contact-row" style="top:86px">
    <svg width="16" height="14" viewBox="0 0 16 14"><circle cx="8" cy="7" r="6" fill="none" stroke="#a1093a" stroke-width="1.3"/><path d="M6 4c-1 1-1 5 0 6l1-1c-.5-1-.5-3 0-4z" fill="#a1093a"/></svg>
    <span>(555) 014-2290</span></div>
  <div class="abs contact-row" style="top:114px">
    <svg width="16" height="14" viewBox="0 0 16 14"><rect x="2" y="5" width="12" height="8" fill="#a1093a"/><path d="M1 5c2-4 12-4 14 0" fill="none" stroke="#a1093a" stroke-width="2"/></svg>
    <span>(555) 014-2290</span></div>
  <div class="abs contact-row" style="top:143px">
    <svg width="16" height="14" viewBox="0 0 16 14"><rect x="1" y="3" width="14" height="9" fill="#a1093a"/><path d="M1 3l7 5 7-5" fill="none" stroke="#0d0d0d" stroke-width="1"/></svg>
    <span>contact@qrvadvisors-example.com</span></div>
  <div class="abs follow">Follow Us: <i></i><i></i><i></i></div>
  <div class="abs foot-brand"><i></i>QRV Advisors</div>
  <div class="abs copy">© 2014 QRV ADVISORS.<br>All rights reserved.</div>
</footer>
</body>
</html>
```